New design for Comparison website

We need new design for our website https://prisvaktposten.no/ . We compare prices and providers in different niches such as electricity, mobile plans, broadband etc.

We would like to see design like Tarivo com or our competitor kjøpklokt no

We will need design of all pages, with tables, tables are somewhat different depending on the service compared (use kjøpklokt no for reference) . Our focus is CTR through comparison Tables.

Final design must communicate following: Professionalism, thrust, authority.

Number of Pages Required

5+ page

Font styles to use
Sans Serif

Colors

Designer to choose colors to be used in the design.

Requirements
Must have
• Tables
Nice to have
• Images in content

```html
<!DOCTYPE html>
<html lang="en">
<head>
<meta charset="utf-8">
<title>Prisvaktposten – Compare Prices</title>
<link href="https://fonts.googleapis.com/css2?family=Open+Sans:wght@400;600;700;800&display=swap" rel="stylesheet">
<style>
:root{
  --green:#1fa35f;
  --green-dark:#178a4f;
  --ink:#333a40;
  --muted:#8a9096;
  --line:#e4e7ea;
  --paper:#ffffff;
  --section:#f2f3f5;
  --dark:#2b2f33;
  --blue:#3ba6e0;
  --coral:#e85b5b;
  --orange:#f39a32;
  --cyan:#2fb2d8;
}
*{box-sizing:border-box;margin:0;padding:0}
html,body{width:1200px;height:2224px;overflow:hidden}
body{font-family:"Open Sans",Arial,sans-serif;color:var(--ink);background:var(--paper);font-size:14px}
.wrap{width:1060px;margin:0 auto;position:relative}

/* header */
.site-header{height:60px;background:var(--paper);box-shadow:0 1px 3px rgba(0,0,0,.08);position:relative;z-index:2}
.site-header .wrap{display:flex;align-items:center;justify-content:space-between;height:60px}
.brand{display:flex;align-items:center;gap:10px;font-weight:700;font-size:22px;color:var(--green)}
.brand-mark{width:26px;height:26px;background:var(--green);border-radius:3px}
.main-nav{display:flex;gap:30px;align-items:center;font-size:11px;font-weight:700;letter-spacing:.3px}
.main-nav a{color:var(--ink);text-decoration:none}
.main-nav a.active{color:var(--green)}

/* hero */
.hero{height:520px;position:relative;overflow:hidden}
.hero-photo{position:absolute;inset:0;background:linear-gradient(100deg,#8c8f91 0%,#5d5f61 35%,#7b6f66 60%,#3b3a39 100%)}
.hero-photo::after{content:"";position:absolute;inset:0;background:rgba(30,30,30,.35)}
.hero-copy{position:absolute;right:140px;top:150px;width:430px;color:#fff}
.hero-brand{display:flex;align-items:center;gap:10px;font-size:26px;font-weight:700;opacity:.85;margin-bottom:14px}
.hero-brand span{width:28px;height:28px;background:#fff;border-radius:3px;opacity:.8}
.hero h1{font-size:54px;font-weight:800;letter-spacing:1px;line-height:1.05}
.hero p{font-size:15px;line-height:1.5;margin:12px 0 26px;color:#f0f0f0}
.btn{display:inline-block;background:var(--green);color:#fff;font-size:12px;font-weight:700;padding:12px 24px;border-radius:3px;text-decoration:none}
.slider-dots{position:absolute;left:130px;bottom:40px;display:flex;gap:8px}
.slider-dots i{width:10px;height:10px;border-radius:50%;background:rgba(255,255,255,.5)}
.slider-dots i:first-child{background:#fff}

/* how it works */
.section-title{text-align:center;font-size:26px;font-weight:700;letter-spacing:.5px}
.section-title::after{content:"";display:block;width:60px;height:3px;background:var(--green);margin:12px auto 0}
.how{height:500px;padding-top:58px}
.steps{display:flex;justify-content:space-between;width:900px;margin:58px auto 0;position:relative}
.steps::before{content:"";position:absolute;top:58px;left:150px;right:150px;border-top:2px dashed #cfd4d8}
.step{width:300px;text-align:center;position:relative}
.step-icon{width:116px;height:116px;border-radius:50%;margin:0 auto;display:flex;align-items:center;justify-content:center;border:6px solid #fff;box-shadow:0 0 0 2px var(--line)}
.step-icon.orange{background:var(--orange)}
.step-icon.green{background:var(--green)}
.step-icon.blue{background:var(--blue)}
.step h3{font-size:15px;font-weight:700;margin-top:22px}
.step .sub{font-size:11px;color:var(--muted);margin-top:4px}
.step p{font-size:12px;line-height:1.6;color:var(--muted);margin-top:14px;padding:0 14px}

/* comparison tables */
.compare{height:500px;background:var(--section);padding-top:40px}
.cards{display:flex;justify-content:space-between;width:940px;margin:44px auto 0}
.card{width:218px;background:#fff;box-shadow:0 1px 4px rgba(0,0,0,.1);text-align:center;padding-bottom:18px}
.card-head{height:38px;line-height:38px;color:#fff;font-weight:700;font-size:14px}
.electricity .card-head{background:var(--blue)}
.mobile .card-head{background:var(--coral)}
.broadband .card-head{background:var(--orange)}
.guides .card-head{background:var(--cyan)}
.card-price{height:82px;display:flex;align-items:center;justify-content:center;color:#fff;font-size:32px;font-weight:700;background:linear-gradient(135deg,#55595c,#2e3134)}
.card ul{list-style:none;text-align:left;padding:8px 22px 14px}
.card li{font-size:11px;color:var(--muted);padding:8px 0;border-bottom:1px solid var(--line);display:flex;align-items:center;gap:8px}
.card li::before{content:"";width:7px;height:7px;border-radius:50%;flex:none}
.electricity li::before,.electricity .btn{background:var(--blue)}
.mobile li::before,.mobile .btn{background:var(--coral)}
.broadband li::before,.broadband .btn{background:var(--orange)}
.guides li::before,.guides .btn{background:var(--cyan)}
.card .btn{font-size:10px;padding:8px 16px}

/* testimonials */
.testimonials{height:300px;position:relative;color:#fff}
.testimonials-bg{position:absolute;inset:0;background:linear-gradient(90deg,#3a3d40,#25282b 50%,#3a3d40)}
.testimonials .inner{position:relative;padding-top:38px}
.testimonials .section-title{color:#fff}
.quote{display:flex;gap:26px;width:820px;margin:42px auto 0;align-items:flex-start}
.avatar{width:84px;height:84px;border-radius:50%;background:#8a7e74;border:3px solid #fff;flex:none}
.quote p{font-size:13px;line-height:1.65;color:#e6e6e6}
.quote .who{font-size:12px;font-weight:700;margin-top:10px}
.quote .role{font-size:10px;color:#bbb}
.stars{margin-top:6px;display:flex;gap:3px}
.arrow{position:absolute;top:150px;width:30px;height:30px;border-radius:50%;background:rgba(255,255,255,.15);display:flex;align-items:center;justify-content:center}
.arrow.prev{left:70px}.arrow.next{right:70px}

/* newsletter */
.newsletter{height:100px;background:var(--green);color:#fff}
.newsletter .wrap{display:flex;align-items:center;height:100px;gap:24px}
.newsletter h2{font-size:20px;font-weight:700}
.newsletter p{font-size:12px;opacity:.9;margin-top:3px}
.subscribe{margin-left:auto;display:flex}
.subscribe span{width:300px;height:40px;background:#fff;color:#aaa;font-size:12px;line-height:40px;padding-left:14px}
.subscribe b{height:40px;line-height:40px;padding:0 22px;background:var(--dark);font-size:12px}

/* footer */
.site-footer{height:294px;background:#f7f8f9;padding-top:34px}
.site-footer .wrap{display:flex;gap:40px}
.foot-col{width:150px}
.foot-col h4{font-size:12px;font-weight:700;margin-bottom:14px}
.foot-col a{display:block;font-size:11px;color:var(--muted);text-decoration:none;margin-bottom:8px}
.social a{display:flex;align-items:center;gap:8px}
.social a::before{content:"";width:18px;height:18px;border-radius:50%;background:#c8cdd2}
.social-box{margin-left:auto;width:250px;height:170px;border:1px solid var(--line);background:#fff;padding:10px}
.social-box .title{font-size:11px;font-weight:700;margin-bottom:8px}
.social-box .feed{height:120px;background:linear-gradient(135deg,#d6dade,#b9bfc5)}
.copyright{height:34px;background:#fff;border-top:1px solid var(--line);text-align:center;font-size:11px;color:var(--muted);line-height:34px}
</style>
</head>
<body>

<header class="site-header">
  <div class="wrap">
    <div class="brand"><span class="brand-mark"></span>Prisvaktposten</div>
    <nav class="main-nav">
      <a class="active" href="#">HOME</a>
      <a href="#">PROVIDERS</a>
      <a href="#">NEW</a>
      <a href="#">CLIENTS</a>
      <a href="#">HOSTING AND DOMAINS</a>
      <a href="#">RESIDENTIAL ALARM</a>
      <svg width="14" height="14" viewBox="0 0 14 14"><circle cx="6" cy="6" r="4.5" fill="none" stroke="#333a40" stroke-width="1.8"/><line x1="9.3" y1="9.3" x2="13" y2="13" stroke="#333a40" stroke-width="1.8"/></svg>
    </nav>
  </div>
</header>

<section class="hero">
  <div class="hero-photo" role="img" aria-label="Photo of hands holding a smartphone over a desk"></div>
  <div class="hero-copy">
    <div class="hero-brand"><span></span>Prisvaktposten</div>
    <h1>COMPARE PRICES</h1>
    <p>Find the best deal on power, mobile and broadband in minutes. Compare trusted providers side by side and save.</p>
    <a class="btn" href="#">GET STARTED TODAY</a>
  </div>
  <div class="slider-dots"><i></i><i></i></div>
</section>

<section class="how">
  <h2 class="section-title">HOW IT WORKS</h2>
  <div class="steps">
    <div class="step">
      <div class="step-icon orange"><svg width="46" height="46" viewBox="0 0 46 46" fill="#fff"><rect x="6" y="8" width="6" height="6"/><rect x="16" y="9" width="24" height="4"/><rect x="6" y="20" width="6" height="6"/><rect x="16" y="21" width="24" height="4"/><rect x="6" y="32" width="6" height="6"/><rect x="16" y="33" width="24" height="4"/></svg></div>
      <h3>SELECT CATEGORY</h3>
      <div class="sub">Pick what you need</div>
      <p>Choose electricity, mobile plans or broadband and tell us a little about your home and usage.</p>
    </div>
    <div class="step">
      <div class="step-icon green"><svg width="46" height="46" viewBox="0 0 46 46" fill="#fff"><rect x="6" y="24" width="8" height="16"/><rect x="19" y="14" width="8" height="26"/><rect x="32" y="6" width="8" height="34"/></svg></div>
      <h3>COMPARE PROVIDERS</h3>
      <div class="sub">See every offer side by side</div>
      <p>Our tables rank prices and terms from all providers so you can spot the best value at a glance.</p>
    </div>
    <div class="step">
      <div class="step-icon blue"><svg width="46" height="46" viewBox="0 0 46 46" fill="none" stroke="#fff" stroke-width="3"><path d="M4 8h6l5 20h20l5-14H13"/><circle cx="18" cy="36" r="3" fill="#fff"/><circle cx="32" cy="36" r="3" fill="#fff"/></svg></div>
      <h3>ORDER SERVICE</h3>
      <div class="sub">Switch in a few clicks</div>
      <p>Order your new deal directly and we handle the switch, with no fees and no paperwork for you.</p>
    </div>
  </div>
</section>

<section class="compare">
  <h2 class="section-title">COMPARISON TABLES</h2>
  <div class="cards">
    <div class="card electricity">
      <div class="card-head">ELECTRICITY</div>
      <div class="card-price" role="img" aria-label="Photo of a power line">$26.00</div>
      <ul><li>Fixed price for twelve months</li><li>No start-up fee</li><li>Green power option</li><li>Free monthly invoice</li></ul>
      <a class="btn" href="#">LEARN MORE</a>
    </div>
    <div class="card mobile">
      <div class="card-head">MOBILE PLANS</div>
      <div class="card-price" role="img" aria-label="Photo of a mobile phone">$18.00</div>
      <ul><li>Unlimited calls and texts</li><li>Data rollover included</li><li>Free roaming in EU</li><li>No binding period</li></ul>
      <a class="btn" href="#">LEARN MORE</a>
    </div>
    <div class="card broadband">
      <div class="card-head">BROADBAND</div>
      <div class="card-price" role="img" aria-label="Photo of a network router">$26.00</div>
      <ul><li>Speeds up to 500 Mbit</li><li>Free router included</li><li>Quick installation</li><li>Local support team</li></ul>
      <a class="btn" href="#">LEARN MORE</a>
    </div>
    <div class="card guides">
      <div class="card-head">WINNING GUIDES</div>
      <div class="card-price" role="img" aria-label="Photo of a laptop on a desk">$26.00</div>
      <ul><li>Expert buying advice</li><li>Updated every week</li><li>Tips to cut your bills</li><li>Clear honest reviews</li></ul>
      <a class="btn" href="#">LEARN MORE</a>
    </div>
  </div>
</section>

<section class="testimonials">
  <div class="testimonials-bg" role="img" aria-label="Dark photo of an office workspace"></div>
  <div class="inner">
    <h2 class="section-title">WHAT OUR CUSTOMER SAY'S</h2>
    <div class="quote">
      <div class="avatar" role="img" aria-label="Customer portrait"></div>
      <div>
        <p>"I saved almost a third on my power bill after one quick comparison. The tables made it easy to see which provider fit my home, and switching took only a few minutes. I now check every service here before I sign anything new."</p>
        <div class="who">KAMILLA STRAND</div>
        <div class="role">Happy customer</div>
        <div class="stars">
          <svg width="70" height="13" viewBox="0 0 70 13" fill="#f5b82e"><path id="s" d="M6.5 0l2 4.2 4.5.6-3.3 3.1.8 4.6-4-2.2-4 2.2.8-4.6L0 4.8l4.5-.6z"/><use href="#s" x="14"/><use href="#s" x="28"/><use href="#s" x="42"/><use href="#s" x="56" fill="#777"/></svg>
        </div>
      </div>
    </div>
  </div>
  <div class="arrow prev"><svg width="10" height="12" viewBox="0 0 10 12"><path d="M8 1L3 6l5 5" fill="none" stroke="#fff" stroke-width="2"/></svg></div>
  <div class="arrow next"><svg width="10" height="12" viewBox="0 0 10 12"><path d="M2 1l5 5-5 5" fill="none" stroke="#fff" stroke-width="2"/></svg></div>
</section>

<section class="newsletter">
  <div class="wrap">
    <svg width="44" height="32" viewBox="0 0 44 32"><rect x="1" y="1" width="42" height="30" rx="2" fill="none" stroke="#fff" stroke-width="2"/><path d="M1 2l21 16L43 2" fill="none" stroke="#fff" stroke-width="2"/></svg>
    <div>
      <h2>SUBSCRIBE TO OUR NEWSLETTER</h2>
      <p>Get the best new deals and price drops sent straight to your inbox every week.</p>
    </div>
    <div class="subscribe"><span>Enter your email address</span><b>SUBSCRIBE</b></div>
  </div>
</section>

<footer class="site-footer">
  <div class="wrap">
    <div class="foot-col">
      <h4>RELATED PAGES</h4>
      <a href="#">Home</a><a href="#">About Us</a><a href="#">Contact</a><a href="#">Blog</a><a href="#">Terms</a><a href="#">Privacy</a><a href="#">Cookies</a>
    </div>
    <div class="foot-col">
      <h4>COMPARE SERVICES</h4>
      <a href="#">Electricity</a><a href="#">Mobile plans</a><a href="#">Web hosting</a><a href="#">Residential alarm</a><a href="#">Broadband</a>
    </div>
    <div class="foot-col">
      <h4>NAVIGATION</h4>
      <a href="#">Providers</a><a href="#">News</a><a href="#">Clients</a><a href="#">Hosting &amp; domains</a>
    </div>
    <div class="foot-col social">
      <h4>FOLLOW US</h4>
      <a href="#">Social feed</a><a href="#">News feed</a><a href="#">Community</a><a href="#">Video channel</a>
    </div>
    <div class="social-box">
      <div class="title">Prisvaktposten on social</div>
      <div class="feed" role="img" aria-label="Social page preview with follower photos"></div>
    </div>
  </div>
</footer>
<div class="copyright">Copyright © Prisvaktposten – 2017 | All rights reserved</div>

</body>
</html>
```